Re-design and craft the perfect CV platform

We are building a CV-based platform designed to connect employees and employers, with a strong focus on individual users. As we're just starting out, we're looking to have our platform and logo redesigned to better reflect our vision
https://app.zelvorhire.com/
Colors like in the logo attached
#87C032 #6A6E71 #618930 - also you can add more colors if you like.
https://app.zelvorhire.com/dashboard - This page would be nice if you plan it, like personal Bio dashboard. Attached picture (Dashboard wanted) one idea from how we would like to be, but we are open for new professional ideas/solutions.
https://app.zelvorhire.com/posts - On this page we want to be showed the jobs posted. Attached one picture about our idea (jobs page wanted)
https://app.zelvorhire.com/profile - design something nice.
Only Photoshop, Illustrator or Framekit
Other pictures from the app attached (as looking right now)

Target Market(s)

Job seekers, HR, Recruiters

Industry/Entity Type

HR Tech

Number of Pages Required

5+ page

Colors
00AB8E
00BBA5
67D7C9
C6EFE9
E9F9F6

```html
<!DOCTYPE html>
<html lang="en">
<head>
<meta charset="utf-8">
<title>CVNEXA – Recruitment web app</title>
<link href="https://fonts.googleapis.com/css2?family=Poppins:wght@400;500;600;700&display=swap" rel="stylesheet">
<style>
:root{
  --teal:#00AB8E; --teal2:#00BBA5; --mint:#67D7C9; --pale:#C6EFE9; --wash:#E9F9F6;
  --ink:#2b3437; --grey:#8b9396; --line:#e4e9ea; --soft:#f3f6f6; --red:#f07a86;
}
*{box-sizing:border-box;margin:0;padding:0}
html,body{width:1200px;height:3188px;overflow:hidden}
body{font-family:'Poppins',sans-serif;color:var(--ink);background:#fff;position:relative}
.abs{position:absolute}
.wash{background:linear-gradient(180deg,#fff 0%,var(--wash) 40%,#fff 70%,var(--wash) 100%)}
.hero{left:0;top:0;width:1200px;height:958px;background:linear-gradient(160deg,#fff 30%,var(--wash) 100%);overflow:hidden}
.brand{left:109px;top:140px;font-weight:700;font-size:46px;color:var(--teal);letter-spacing:1px;display:flex;align-items:center;gap:14px}
.brand i{width:34px;height:34px;border-radius:50%;background:var(--teal);display:block}
.tilt{transform:rotate(-28deg);transform-origin:0 0;box-shadow:0 18px 40px rgba(0,80,70,.18);border-radius:6px;overflow:hidden;background:#f6f8f8}
.tilt .bar{height:34px;background:var(--teal)}
.tilt .row{height:10px;background:var(--line);margin:12px 18px;border-radius:4px}
.tilt .row.s{width:40%}
.band{left:0;top:958px;width:1200px;height:32px;background:var(--teal)}
.login-stage{left:110px;top:1060px;width:986px;height:554px;background:linear-gradient(100deg,#3d4a52 0%,#6d7a80 40%,#252a2d 70%,#111 100%);box-shadow:0 20px 40px rgba(0,0,0,.15)}
.ghost-v{font-weight:700;color:#e8ecec;font-size:150px;writing-mode:vertical-rl;line-height:1}
.login-card{left:626px;top:1157px;width:359px;height:361px;background:#fff;border-radius:6px;padding:0 32px;text-align:center}
.login-card .tab{position:absolute;left:66px;top:0;width:226px;height:6px;background:var(--teal);border-radius:0 0 6px 6px}
.login-card .name{margin-top:50px;font-size:27px;font-weight:700;color:var(--teal);display:flex;justify-content:center;align-items:center;gap:8px}
.login-card .name i{width:20px;height:20px;border-radius:50%;background:var(--teal)}
.login-card h2{font-size:16px;font-weight:600;margin-top:18px}
.login-card p{font-size:11px;margin-top:8px;color:#555}
.login-card label{display:block;text-align:left;font-size:10.5px;font-weight:600;margin-top:40px}
.field{margin-top:10px;height:40px;background:#f1f3f3;border-radius:4px;display:flex;align-items:center;padding-left:14px;gap:12px;font-size:10.5px;color:#9aa}
.btn{display:inline-flex;align-items:center;gap:6px;background:var(--teal);color:#fff;font-weight:600;font-size:15px;border-radius:4px;height:40px;padding:0 26px}
.login-card .btn{position:absolute;left:32px;top:290px}
.app{left:110px;width:986px;height:553px;background:var(--soft);box-shadow:0 18px 40px rgba(0,80,70,.12)}
.head{height:60px;background:var(--teal);position:relative;color:#fff}
.head .logo{position:absolute;left:28px;top:17px;font-weight:700;font-size:19px;display:flex;gap:6px;align-items:center}
.head .logo i{width:14px;height:14px;border-radius:50%;background:#fff}
.tab-item{position:absolute;top:20px;font-size:13.5px;font-weight:500;display:flex;align-items:center;gap:6px;white-space:nowrap}
.tab-item.on{top:10px;height:50px;width:100px;background:var(--soft);color:var(--teal);border-radius:18px 18px 0 0;justify-content:center}
.ico{position:absolute;top:20px;width:18px;height:18px}
.avatar{position:absolute;top:12px;width:32px;height:32px;border-radius:50%;background:linear-gradient(#7d8fcf,#2f3a73);border:2px solid #fff}
.card{position:absolute;background:#fff;border-radius:6px}
.t{font-size:8px;color:var(--grey);line-height:1.55}
.h{font-size:11px;font-weight:600}
.g{color:var(--teal)}
.person{text-align:center}
.person .pic{width:54px;height:54px;border-radius:50%;background:linear-gradient(#8196d8,#2b3570);margin:12px auto 8px}
.meta{display:flex;justify-content:space-around;margin:14px 14px 0;font-size:8px;text-align:center}
.langs{display:flex;justify-content:space-around;margin-top:10px}
.ring{width:30px;height:30px;border-radius:50%;border:4px solid #d9dede;margin:0 auto 6px;display:flex;align-items:center;justify-content:center;font-size:6px;color:#fff}
.ring b{width:18px;height:18px;border-radius:50%;background:#aaa;display:flex;align-items:center;justify-content:center;font-weight:500}
.edu{display:flex;gap:8px;align-items:flex-start;width:32%}
.dot{width:20px;height:20px;border-radius:50%;background:var(--soft);flex:none;display:flex;align-items:center;justify-content:center}
.dot::after{content:"";width:8px;height:5px;background:var(--teal);border-radius:2px}
.work{background:var(--soft);border-radius:4px;padding:8px 10px;height:46px}
.skill{display:flex;align-items:center;font-size:7.5px;color:var(--grey);height:19.5px}
.skill span{flex:1}
.skill .track{width:56px;height:3px;background:var(--pale);margin-right:12px;position:relative}
.skill .track b{position:absolute;left:0;top:0;height:3px;background:var(--teal)}
.job{border:1px solid var(--line);border-radius:6px;padding:12px 12px;position:relative;width:155px;height:188px}
.job .co{width:14px;height:14px;border-radius:50%;display:block}
.job .fav{position:absolute;right:12px;top:14px;width:8px;height:8px;background:var(--mint);border-radius:50%}
.job h4{font-size:11.5px;font-weight:500;line-height:1.35;margin-top:8px;height:32px}
.stars{color:var(--teal);font-size:10px;letter-spacing:1px}
.stars small{color:#999;font-size:6px;letter-spacing:0;text-decoration:underline;margin-left:4px}
.chips{display:flex;gap:4px;margin-top:6px}
.chips span{border:1px solid #aaa;border-radius:3px;font-size:6px;padding:2px 5px;color:#666}
.pay{display:flex;justify-content:space-between;align-items:baseline;margin-top:18px;font-size:12px}
.pay small{font-size:6px}
.pay em{font-style:normal;font-size:6.5px;color:var(--teal)}
.apply{margin-top:10px;height:16px;border-radius:3px;background:#cdd2d3;color:#fff;font-size:7px;display:flex;align-items:center;justify-content:center}
.apply.on{background:var(--teal)}
.fl{font-size:8px;color:var(--grey);display:flex;align-items:center;gap:6px;height:17px}
.fl i{width:9px;height:9px;border:1px solid var(--teal);border-radius:2px}
.fl i.off{border-color:#ccc}
.fl i.r{border-radius:50%}
.fl i.on{background:var(--teal)}
.fh{font-size:10px;font-weight:500;margin:12px 0 4px}
.ghost{font-weight:700;color:#eef2f2;line-height:1}
.wave{left:0;top:2820px;width:1200px;height:368px}
.thanks{left:0;top:3060px;width:1200px;text-align:center;color:#fff;font-size:42px;font-weight:600}
</style>
</head>
<body>
<div class="abs wash" style="left:0;top:990px;width:1200px;height:2198px"></div>

<section class="abs hero" aria-label="Presentation cover">
  <div class="abs brand"><i></i>CVNEXA</div>
  <div class="abs tilt" style="left:150px;top:470px;width:560px;height:330px">
    <div role="img" aria-label="Photo of a professional man working at a laptop" style="width:100%;height:100%;background:linear-gradient(100deg,#3d4a52,#6d7a80 45%,#1a1d1f)"></div>
    <div class="abs" style="left:300px;top:40px;width:200px;height:210px;background:#fff;border-radius:5px;padding:30px 20px">
      <div style="font-weight:700;color:var(--teal);font-size:16px">CVNEXA</div>
      <div class="row" style="margin:18px 0 0"></div><div class="row s" style="margin:8px 0 0"></div>
      <div style="margin-top:30px;height:22px;background:var(--soft);border-radius:3px"></div>
      <div style="margin-top:12px;width:60px;height:20px;background:var(--teal);border-radius:3px"></div>
    </div>
  </div>
  <div class="abs tilt" style="left:660px;top:160px;width:560px;height:320px"><div class="bar"></div><div class="row"></div><div class="row s"></div><div class="row"></div><div class="row s"></div><div class="row"></div><div class="row"></div></div>
  <div class="abs tilt" style="left:600px;top:590px;width:560px;height:320px"><div class="bar"></div><div class="row"></div><div class="row"></div><div class="row s"></div><div class="row"></div><div class="row s"></div><div class="row"></div></div>
  <div class="abs tilt" style="left:70px;top:890px;width:560px;height:320px"><div class="bar"></div><div class="row"></div><div class="row s"></div><div class="row"></div></div>
  <div class="abs tilt" style="left:620px;top:940px;width:560px;height:320px"><div class="bar"></div><div class="row"></div></div>
  <div class="abs tilt" style="left:1000px;top:720px;width:560px;height:320px"><div class="bar"></div><div class="row"></div><div class="row s"></div></div>
  <div class="abs tilt" style="left:1100px;top:10px;width:300px;height:200px"><div class="bar"></div><div class="row"></div></div>
</section>
<div class="abs band"></div>

<div class="abs ghost-v" style="left:1045px;top:1090px">Login</div>
<div class="abs login-stage" role="img" aria-label="Photo of a young professional man thinking at a laptop"></div>
<div class="abs login-card">
  <div class="tab"></div>
  <div class="name"><i></i>CVNEXA</div>
  <h2>Recruitment web app access</h2>
  <p>Login to your account to continue</p>
  <label>Email Address</label>
  <div class="field"><svg width="11" height="11" viewBox="0 0 12 12"><circle cx="6" cy="3.5" r="2.8" fill="#333"/><path d="M1 12c0-3 2.2-5 5-5s5 2 5 5z" fill="#333"/></svg>Enter Email Address</div>
  <div class="btn">Login <svg width="10" height="10" viewBox="0 0 10 10"><path d="M1 5h7M5 2l3 3-3 3" stroke="#fff" fill="none" stroke-width="1.2"/></svg></div>
</div>

<div class="abs ghost" style="left:25px;top:2180px;font-size:120px;transform:rotate(-90deg);transform-origin:0 0">CV</div>
<div class="abs app" style="top:1752px">
  <div class="head">
    <div class="logo"><i></i>CVNEXA</div>
    <div class="tab-item" style="left:330px">▪ Jobs</div>
    <div class="tab-item on" style="left:402px">▪ CV</div>
    <div class="tab-item" style="left:527px">● Notification</div>
    <div class="avatar" style="left:838px"></div>
    <svg class="ico" style="left:886px" viewBox="0 0 18 18"><path d="M2 3h14v9H7l-4 3v-3H2z" fill="#fff"/></svg>
    <svg class="ico" style="left:916px" viewBox="0 0 18 18"><path d="M9 16L2 9a4 4 0 0 1 7-5 4 4 0 0 1 7 5z" fill="#fff"/></svg>
    <svg class="ico" style="left:946px" viewBox="0 0 18 18"><circle cx="9" cy="9" r="6" fill="none" stroke="#fff" stroke-width="4" stroke-dasharray="3 2"/><circle cx="9" cy="9" r="2.5" fill="#fff"/></svg>
  </div>

  <div class="card person" style="left:25px;top:79px;width:203px;height:449px">
    <div class="pic" role="img" aria-label="Profile photo"></div>
    <div class="h">Marela Tovins</div>
    <div class="t" style="font-size:7px">UI/UX DESIGNER</div>
    <div class="meta"><div><div class="g">Age</div><div class="t">32 Year</div></div><div style="border-left:1px solid var(--line)"></div><div><div class="g">Gender</div><div class="t">Female</div></div></div>
    <div style="border-top:1px solid var(--line);margin:18px 14px 0"></div>
    <div class="h" style="font-size:9px;margin-top:12px;font-weight:500">Contact Info</div>
    <div style="text-align:left;padding:0 14px;margin-top:10px">
      <div style="display:flex;gap:10px;align-items:center"><span class="dot" style="background:var(--wash)"></span><div><div class="g" style="font-size:7.5px">Email Address</div><div class="t">info@marelatovins.com</div></div></div>
      <div style="display:flex;gap:10px;align-items:center;margin-top:10px"><span class="dot" style="background:var(--wash)"></span><div><div class="g" style="font-size:7.5px">Phone Number</div><div class="t">+1 555 014 7290</div></div></div>
    </div>
    <div style="border-top:1px solid var(--line);margin:14px 14px 0"></div>
    <div class="h" style="font-size:9px;margin-top:10px;font-weight:500">Language</div>
    <div class="langs">
      <div><div class="ring"><b>50%</b></div><div class="t">English</div></div>
      <div><div class="ring" style="border-color:var(--pale)"><b style="background:var(--mint)">50%</b></div><div class="t">Spanish</div></div>
      <div><div class="ring" style="border-color:var(--teal)"><b style="background:var(--teal)">50%</b></div><div class="t">Deutsch</div></div>
    </div>
    <div style="border-top:1px solid var(--line);margin:14px 14px 0"></div>
    <div class="h" style="font-size:9px;margin-top:10px;font-weight:500">Driver License</div>
    <div style="display:flex;gap:10px;align-items:center;text-align:left;padding:0 14px;margin-top:8px">
      <span class="dot" style="background:var(--soft)"></span>
      <div><div style="font-size:7.5px;font-weight:500">Driver's Licence Western Australia</div><div class="t" style="font-size:6.5px">Licence Number &nbsp; 8120456<br>Expiry Date &nbsp;&nbsp;&nbsp; 17 Jan 2026</div></div>
    </div>
  </div>

  <div class="card" style="left:249px;top:79px;width:486px;height:449px;padding:18px 18px">
    <div style="display:flex;justify-content:space-between;align-items:center">
      <div class="h" style="font-size:12.5px;font-weight:500">Experience</div>
      <div class="t" style="color:var(--ink)">Years of work experience: <span style="background:var(--teal);color:#fff;padding:2px 5px;border-radius:3px;font-weight:600">15 years</span></div>
    </div>
    <div style="border-top:1px solid var(--line);margin:12px 0"></div>
    <div style="font-size:8.5px;font-weight:500">About</div>
    <p class="t" style="margin-top:6px">I'm a Product Designer based in Melbourne, Australia. I enjoy working on product design and web projects. I occasionally take on freelance work.</p>
    <p class="t" style="margin-top:8px">I've worked with some of the world's most exciting companies, including Paylane, Cobrix, and Tallow. I'm passionate about helping startups grow, improve their UX and customer experience, and to fundraise through good design.</p>
    <p class="t" style="margin-top:8px">My work has been featured on Fontnest, Mindgrid Magazine, Sitecraft, Glyph Shelf, Layout Prize, Pagester, Webmuse and Top Page Archive</p>
    <div class="g" style="font-size:7px;margin-top:6px">Read More</div>
    <div style="border-top:1px solid var(--line);margin:12px 0 10px"></div>
    <div style="font-size:8.5px;font-weight:500">Education</div>
    <div style="display:flex;justify-content:space-between;margin-top:8px">
      <div class="edu"><span class="dot"></span><div><div style="font-size:7.5px;font-weight:600">Course Studies (School)</div><div class="t" style="font-size:6.5px">Computer science<br>2007 - 2009</div></div></div>
      <div class="edu"><span class="dot"></span><div><div style="font-size:7.5px;font-weight:600">Varnell College</div><div class="t" style="font-size:6.5px">Studies of Business Management<br>2009 - 2013</div></div></div>
      <div class="edu"><span class="dot"></span><div><div style="font-size:7.5px;font-weight:600">Varnell University</div><div class="t" style="font-size:6.5px">Bachelor of Business Management<br>2013 - 2017</div></div></div>
    </div>
    <div style="border-top:1px solid var(--line);margin:12px 0 10px"></div>
    <div style="font-size:8.5px;font-weight:500">Work Experience</div>
    <div style="display:grid;grid-template-columns:1fr 1fr;gap:8px;margin-top:8px">
      <div class="work"><div style="font-size:7.5px;font-weight:600">Studio Kelvane Canberra Australia</div><div class="t" style="font-size:6.5px">Jr. Graphic Designer<br>2007 - 2009</div></div>
      <div class="work"><div style="font-size:7.5px;font-weight:600">Digital Marketing Agency</div><div class="t" style="font-size:6.5px">Graphic Designer<br>2009 - 2011</div></div>
      <div class="work"><div style="font-size:7.5px;font-weight:600">Ostrane Corp. Kota Baru - Singapore</div><div class="t" style="font-size:6.5px">UI/UX Designer<br>2011 - 2014</div></div>
      <div class="work"><div style="font-size:7.5px;font-weight:600">Studio Kelvane Sydney Australia</div><div class="t" style="font-size:6.5px">Project Manager<br>2014 - 2018</div></div>
    </div>
    <div class="g" style="font-size:6.5px;text-align:center;margin-top:10px">Read More</div>
    <div class="abs" style="right:2px;top:55px;width:3px;height:170px;background:var(--teal);border-radius:2px"></div>
  </div>

  <div class="card" style="left:763px;top:79px;width:200px;height:217px;padding:14px 16px">
    <div style="display:flex;justify-content:space-between"><div style="font-size:10px;font-weight:500">Last Activites</div><div class="g" style="font-size:7px">See All</div></div>
    <div style="display:flex;gap:12px;align-items:center;margin-top:22px"><span style="width:22px;height:22px;border-radius:50%;background:var(--pale);flex:none"></span><div class="t">Your Application has <b style="color:var(--ink);font-weight:500">accept<br>3 Companies</b></div></div>
    <div style="display:flex;gap:12px;align-items:center;margin-top:16px"><span style="width:22px;height:22px;border-radius:50%;background:var(--red);color:#fff;font-size:9px;display:flex;align-items:center;justify-content:center;flex:none">×</span><div class="t">Your Application has <b style="color:var(--ink);font-weight:500">rejected<br>1 Companies</b></div></div>
  </div>

  <div class="card" style="left:763px;top:317px;width:200px;height:214px;padding:12px 14px">
    <div style="font-size:8.5px;font-weight:500;text-align:center;margin-bottom:16px">Skills</div>
    <div class="skill"><span>Raster Studio</span><div class="track"><b style="width:87%"></b></div>87%</div>
    <div class="skill"><span>Vector Studio 2020</span><div class="track"><b style="width:84%"></b></div>84%</div>
    <div class="skill"><span>Motion Studio</span><div class="track"><b style="width:55%"></b></div>55%</div>
    <div class="skill"><span>Cut Studio</span><div class="track"><b style="width:67%"></b></div>67%</div>
    <div class="skill"><span>Draw Studio</span><div class="track"><b style="width:48%"></b></div>48%</div>
    <div class="skill"><span>Proto Studio</span><div class="track"><b style="width:96%"></b></div>96%</div>
    <div class="skill"><span>Framekit</span><div class="track"><b style="width:91%"></b></div>91%</div>
    <div class="skill"><span>Office Suite</span><div class="track"><b style="width:54%"></b></div>54%</div>
  </div>
</div>

<div class="abs ghost" style="left:40px;top:2372px;font-size:130px;letter-spacing:4px">JOB PORTAL</div>
<svg class="abs wave" viewBox="0 0 1200 368" preserveAspectRatio="none"><defs><linearGradient id="wv" x1="0" y1="0" x2="1" y2="1"><stop offset="0" stop-color="#00AB8E"/><stop offset="1" stop-color="#2fc0a5"/></linearGradient></defs><path d="M0 0 C300 80 700 120 1200 40 L1200 368 L0 368 Z" fill="url(#wv)"/></svg>
<div class="abs app" style="top:2443px;background:#f6f8f8">
  <div class="head">
    <div class="logo"><i></i>CVNEXA</div>
    <div class="tab-item on" style="left:308px">▪ Jobs</div>
    <div class="tab-item" style="left:433px">▪ CV</div>
    <div class="tab-item" style="left:527px">● Notification</div>
    <div class="avatar" style="left:838px"></div>
    <svg class="ico" style="left:886px" viewBox="0 0 18 18"><path d="M2 3h14v9H7l-4 3v-3H2z" fill="#fff"/></svg>
    <svg class="ico" style="left:916px" viewBox="0 0 18 18"><path d="M9 16L2 9a4 4 0 0 1 7-5 4 4 0 0 1 7 5z" fill="#fff"/></svg>
    <svg class="ico" style="left:946px" viewBox="0 0 18 18"><circle cx="9" cy="9" r="6" fill="none" stroke="#fff" stroke-width="4" stroke-dasharray="3 2"/><circle cx="9" cy="9" r="2.5" fill="#fff"/></svg>
  </div>
  <div class="card" style="left:25px;top:73px;width:717px;height:452px;padding:20px 18px">
    <div style="display:flex;justify-content:space-between;align-items:center">
      <div style="font-size:12.5px;font-weight:500">Total jobs <span style="border:1px solid var(--line);border-radius:8px;font-size:6.5px;padding:2px 8px;color:#777;margin-left:6px">115 Found</span></div>
      <div class="t" style="color:#555">Sort by: <span style="background:var(--teal);color:#fff;padding:3px 8px;border-radius:3px;font-weight:500">Urgently hiring ⌄</span></div>
    </div>
    <div style="display:grid;grid-template-columns:repeat(4,155px);column-gap:18px;row-gap:8px;margin-top:16px">
      <div class="job"><span class="co" style="background:#6a8df0"></span><i class="fav"></i><h4>Senior UI/UX<br>Designer</h4><div class="stars">★★★★☆<small>(42 Reviews)</small></div><div class="t">● California, CA</div><div class="chips"><span>Full Time</span><span>Senior Level</span><span>Remote</span></div><div class="pay"><span>$2.5k<small>/Monthly</small></span><em>See Details</em></div><div class="apply on">Apply</div></div>
      <div class="job"><span class="co" style="background:#8a57e6"></span><i class="fav"></i><h4>UI/UX Designer</h4><div class="stars">★★★☆☆<small>(10 Reviews)</small></div><div class="t">● California, CA</div><div class="chips"><span>Full Time</span><span>Senior Level</span></div><div class="pay"><span>$3k<small>/Monthly</small></span><em>See Details</em></div><div class="apply">Apply</div></div>
      <div class="job"><span class="co" style="background:#ef4a6a"></span><i class="fav"></i><h4>Jr. UI/UX<br>Designer</h4><div class="stars">★★★★☆<small>(42 Reviews)</small></div><div class="t">● California, CA</div><div class="chips"><span>Full Time</span><span>Senior Level</span><span>Remote</span></div><div class="pay"><span>$1700<small>/Monthly</small></span><em>See Details</em></div><div class="apply">Apply</div></div>
      <div class="job"><span class="co" style="background:#6a8df0"></span><i class="fav"></i><h4>Jr. UI/UX<br>Designer</h4><div class="stars">★★★★☆<small>(42 Reviews)</small></div><div class="t">● California, CA</div><div class="chips"><span>Full Time</span><span>Senior Level</span></div><div class="pay"><span>$2K<small>/Monthly</small></span><em>See Details</em></div><div class="apply">Apply</div></div>
      <div class="job"><span class="co" style="background:#2fbf5a"></span><i class="fav"></i><h4>Senior UI/UX<br>Designer</h4><div class="stars">★★★★☆<small>(42 Reviews)</small></div><div class="t">● California, CA</div><div class="chips"><span>Full Time</span><span>Senior Level</span><span>Remote</span></div><div class="pay"><span>$2.5k<small>/Monthly</small></span><em>See Details</em></div><div class="apply">Apply</div></div>
      <div class="job"><span class="co" style="background:#f05a2a"></span><i class="fav"></i><h4>UI/UX Designer</h4><div class="stars">★★★☆☆<small>(10 Reviews)</small></div><div class="t">● California, CA</div><div class="chips"><span>Full Time</span><span>Senior Level</span></div><div class="pay"><span>$3k<small>/Monthly</small></span><em>See Details</em></div><div class="apply">Apply</div></div>
      <div class="job"><span class="co" style="background:#ef4a6a"></span><i class="fav"></i><h4>Jr. UI/UX<br>Designer</h4><div class="stars">★★★★☆<small>(42 Reviews)</small></div><div class="t">● California, CA</div><div class="chips"><span>Full Time</span><span>Senior Level</span><span>Remote</span></div><div class="pay"><span>$1700<small>/Monthly</small></span><em>See Details</em></div><div class="apply">Apply</div></div>
      <div class="job"><span class="co" style="background:#6a8df0"></span><i class="fav"></i><h4>Jr. UI/UX<br>Designer</h4><div class="stars">★★★★☆<small>(42 Reviews)</small></div><div class="t">● California, CA</div><div class="chips"><span>Full Time</span><span>Senior Level</span></div><div class="pay"><span>$2K<small>/Monthly</small></span><em>See Details</em></div><div class="apply">Apply</div></div>
    </div>
    <div class="abs" style="right:14px;top:58px;width:3px;height:170px;background:var(--teal);border-radius:2px"></div>
  </div>
  <div class="card" style="left:763px;top:73px;width:200px;height:452px;padding:14px 16px">
    <div style="display:flex;justify-content:space-between;align-items:center"><div style="font-size:11px;font-weight:500"><span class="g">⇥</span> Filter</div><div class="g" style="font-size:7px">Clear all</div></div>
    <div class="fh">Job Type</div>
    <div class="fl"><i></i>Full Time</div><div class="fl"><i class="off"></i>Internship</div><div class="fl"><i></i>Freelance</div><div class="fl"><i class="off"></i>Contractual</div>
    <div class="fh">On Site/Remote</div>
    <div class="fl"><i></i>On Site</div><div class="fl"><i class="off"></i>Hybrid</div><div class="fl"><i></i>Remote</div>
    <div class="fh">Salary Range</div>
    <div class="fl"><i class="r off"></i>Under $ 1000</div><div class="fl"><i class="r off"></i>$ 2500 - $ 5000</div><div class="fl"><i class="r off"></i>$ 1000 - $ 2500</div><div class="fl"><i class="r on"></i>Above $ 2500</div>
    <div class="fh">Others</div>
    <div class="fl"><i></i>On Site</div><div class="fl"><i class="off"></i>Hybrid</div><div class="fl"><i></i>Remote</div>
    <div style="margin-top:16px;height:18px;background:var(--teal);border-radius:3px;color:#fff;font-size:7.5px;display:flex;align-items:center;justify-content:center">Apply</div>
  </div>
</div>

<div class="abs thanks">Thanks For Watching</div>
</body>
</html>
```